Business Card Design using new attached logo

We are a family run Plumbing and Heating firm looking to improve our company image with an improved business card and new logo.We are looking to keep the company colour (Blue) involved in our design

Reason: New logo added which needs to be incorporated on designs

Industry/Entity Type

Business

Contact Information for Business Card

See attachment of all info required.

Requirements
Must have
• We have just picked a new company logo which is attached.
• Could you please provide your business card designs using this logo.
• We are looking for the logo on the back as well as the front with all the info required

```html
<!DOCTYPE html>
<html lang="en">
<head>
<meta charset="utf-8">
<title>Harlow Pipeworks – Business Card</title>
<link href="https://fonts.googleapis.com/css2?family=Cinzel:wght@600&family=Open+Sans:ital,wght@0,400;0,600;1,400&display=swap" rel="stylesheet">
<style>
  :root {
    --stage: #333333;
    --card-white: #ffffff;
    --navy: #1f3b7a;
    --navy-deep: #1b3470;
    --blue-bright: #3a86c9;
    --rule-grey: #9a9a9a;
    --ink: #1e1e1e;
    --icon: #2a3a66;
  }
  html, body {
    margin: 0;
    width: 1200px;
    height: 907px;
    overflow: hidden;
    background: var(--stage);
  }
  .stage {
    position: relative;
    width: 1200px;
    height: 907px;
  }
  .card {
    position: absolute;
    left: 300px;
    width: 600px;
    height: 343px;
    box-shadow: 0 3px 10px rgba(0,0,0,0.5);
    overflow: hidden;
  }
  .card--front { top: 92px; background: var(--card-white); }
  .card--back {
    top: 473px;
    background: radial-gradient(ellipse 62% 70% at 50% 48%, var(--blue-bright) 0%, #2a5ea6 50%, var(--navy-deep) 100%);
  }

  .rule {
    position: absolute; left: 0; width: 100%; height: 3px;
    background: linear-gradient(#c9c9c9, var(--rule-grey));
  }
  .rule--top { top: 31px; }
  .rule--bottom { top: 118px; }

  .name-band {
    position: absolute; left: 0; top: 36px; width: 100%; height: 80px;
    background: linear-gradient(90deg, var(--navy-deep) 0%, #2f6bb2 25%, var(--blue-bright) 50%, #2f6bb2 75%, var(--navy-deep) 100%);
    color: #fff;
    text-align: center;
    font-family: "Cinzel", serif;
    font-weight: 600;
  }
  .name-band__name { display: block; margin-top: 17px; font-size: 23px; letter-spacing: 0.5px; }
  .name-band__title { display: block; margin-top: 0; font-size: 17px; letter-spacing: 0.5px; }

  .brand {
    position: absolute; left: 30px; top: 200px; width: 250px;
    display: flex; align-items: center; gap: 10px;
    font-family: "Open Sans", sans-serif; font-weight: 600;
    font-size: 21px; color: var(--navy);
  }
  .brand__dot { width: 16px; height: 16px; border-radius: 50%; background: var(--navy); flex: none; }

  .divider {
    position: absolute; left: 295px; top: 152px; width: 1px; height: 163px;
    background: #b8b8b8;
  }

  .contact {
    position: absolute; left: 318px; top: 143px;
    font-family: "Open Sans", sans-serif; font-size: 14px; color: var(--ink);
    line-height: 19.5px;
  }
  .contact__address { margin: 0 0 7px; }
  .contact__list { list-style: none; margin: 0; padding: 0; }
  .contact__item { display: flex; align-items: center; height: 22.5px; }
  .contact__icon { width: 14px; height: 14px; margin-left: 1px; margin-right: 10px; flex: none; fill: var(--icon); }

  .brand--back {
    left: 0; top: 152px; width: 100%; justify-content: center;
    color: #fff; font-size: 30px; gap: 14px;
  }
  .brand--back .brand__dot { background: #fff; width: 22px; height: 22px; }

  .tagline {
    position: absolute; left: 0; top: 283px; width: 100%; text-align: center;
    font-family: "Open Sans", sans-serif; font-style: italic; font-size: 15.5px; color: #fff;
    margin: 0;
  }
</style>
</head>
<body>
<main class="stage">
  <section class="card card--front">
    <div class="rule rule--top"></div>
    <header class="name-band">
      <span class="name-band__name">Mark Ellison</span>
      <span class="name-band__title">Director</span>
    </header>
    <div class="rule rule--bottom"></div>

    <div class="brand"><span class="brand__dot"></span><span>Harlow Pipeworks</span></div>

    <div class="divider"></div>

    <address class="contact" style="font-style:normal">
      <p class="contact__address">Harlow Pipeworks Ltd<br>14 Mill Lane, Station Road<br>Sutton, SM14XY</p>
      <ul class="contact__list">
        <li class="contact__item">
          <svg class="contact__icon" viewBox="0 0 16 16"><path d="M4 1l3 3-2 2c1 2 3 4 5 5l2-2 3 3-2 3C7 15 1 9 1 3z"/></svg>
          020 7946 0321
        </li>
        <li class="contact__item">
          <svg class="contact__icon" viewBox="0 0 16 16"><path d="M4 1h7v4H4zM1 6h14v6H1zM4 10h8v5H4z"/></svg>
          020 7946 0457
        </li>
        <li class="contact__item">
          <svg class="contact__icon" viewBox="0 0 16 16"><path d="M4 0h8v16H4zM5.5 2v7h5V2z" fill-rule="evenodd"/></svg>
          07700900184
        </li>
        <li class="contact__item">
          <svg class="contact__icon" viewBox="0 0 16 16"><path d="M1 3h14v10H1zM2 4l6 5 6-5z" fill-rule="evenodd"/></svg>
          markellison@harlowpipeworks.co.uk
        </li>
        <li class="contact__item">
          <svg class="contact__icon" viewBox="0 0 16 16" fill="none" stroke="#2a3a66" stroke-width="1.2"><circle cx="8" cy="8" r="6.5"/><ellipse cx="8" cy="8" rx="3" ry="6.5"/><path d="M1.5 8h13M2.5 5h11M2.5 11h11"/></svg>
          www.harlowpipeworks.co.uk
        </li>
      </ul>
    </address>
  </section>

  <section class="card card--back">
    <div class="brand brand--back"><span class="brand__dot"></span><span>Harlow Pipeworks</span></div>
    <p class="tagline">Plumbing and Heating Services</p>
  </section>
</main>
</body>
</html>
```